Design for the A4 Letterhead, envelope and A4 Folder

Design have to be clean, professional, unique (eye catchy) and high end.
Colors: Yellow (Code: 803C), Darker Grey and Black or white (optional)
Logo can be in white or black

Letterhead:
Contain: 1. Korvane Logo
2. Slogan "MADE WITH PRIDE"
3. Company information:
Korvane Valves Pte. Ltd. (Singapore)
Registration no: 201947215K
Tel: (65) 6418 2904
Fax: (65) 6472 9186
Email: sales@korvanevalves.example
Website: http://www.korvanevalves.example
4. Logo watermark

Envelope:
Contain: 1. Korvane Logo
3. website: http://www.korvanevalves.example and email address:
sales@korvanevalves.example
4. Logo watermark

Folder:
Contain: 1. Korvane Logo
3. Company's information:
Tel: (65) 6418 2904
Fax: (65) 6472 9186
4. QR Code
5. Logo watermark
6. On the inside there is a space to insert business card. Contrast colors
between the inside and cover.
Updates

For the Folder design, please be informed that we would prefer to have the Korvane logo on the left hand side of the cover page, rather than on the right hand side.And also if we could highlight the "Made with Pride" slogan with either the yellow box or black/grey box depending on the background color.For the Envelope design,it does not matter where the position of the logo is. But please also highlight the "Made with Pride" Slogan For the Letterhead design, the position of the logo must be on the left hand side and the slogan must be highlighted. In addition, please include the following company information (only for the letterhead design)Korvane Valves Pte. Ltd. (Singapore)Registration no: 200308878MTel: (65) 6535 3735Fax: (65) 6533 3570Email: sales@dynatechpumps.comWebsite: http://www.korvanevalves.example Added Wednesday, August 2, 2017

Target Market(s)

Business to Business, High End market

Industry/Entity Type

It Professional

Font styles to use
Serif

Requirements
Must have
• Design have to be clean, professional, unique (eye catchy) and high end.
Nice to have
• color contrast but still maintaining the professionalism and the seriousness
Should not have
• Messy look, futuristic look, too crowded

```html
<!DOCTYPE html>
<html lang="en">
<head>
<meta charset="utf-8">
<title>Korvane Valves – Letterhead</title>
<link rel="stylesheet" href="https://fonts.googleapis.com/css2?family=Merriweather:wght@700;900&family=Open+Sans:wght@400;700&display=swap">
<style>
  :root {
    --backdrop: #e6d97e;
    --paper: #ffffff;
    --brand-yellow: #f7e71c;
    --brand-yellow-light: #fbf27a;
    --dark-grey: #3d3d3d;
    --mid-grey: #9a9a9a;
    --soft-grey: #d6d6d6;
    --watermark: #f0f0f0;
    --ink: #111111;
    --text-grey: #555555;
  }
  * { margin: 0; padding: 0; box-sizing: border-box; }
  html, body { width: 1200px; height: 784px; overflow: hidden; }
  body { background: var(--backdrop); position: relative; }

  .letterhead {
    position: absolute;
    left: 338px; top: 22px;
    width: 524px; height: 740px;
    background: var(--paper);
    box-shadow: 0 4px 14px rgba(0,0,0,0.12);
    overflow: hidden;
  }

  .edge-tab { position: absolute; width: 4px; height: 34px; background: var(--dark-grey); }
  .edge-tab::after {
    content: ""; position: absolute; left: 0; top: 34px;
    width: 4px; height: 14px; background: var(--brand-yellow);
  }
  .edge-tab--left { left: 0; top: 30px; }
  .edge-tab--right { right: 0; top: 66px; }

  .brand {
    position: absolute; left: 30px; top: 34px;
    display: flex; align-items: center; gap: 10px;
  }
  .brand__mark {
    width: 26px; height: 26px; border-radius: 50%;
    background: var(--ink);
  }
  .brand__name {
    font-family: "Merriweather", Georgia, serif;
    font-weight: 900; font-size: 22px; letter-spacing: 1px;
    color: var(--ink);
  }

  .contact {
    position: absolute; right: 30px; top: 70px;
    font-family: "Open Sans", Arial, sans-serif;
    font-size: 9.5px; line-height: 1.45; color: var(--text-grey);
    list-style: none;
  }
  .contact__company { font-weight: 700; color: var(--ink); margin-bottom: 1px; }
  .contact__item { display: flex; align-items: center; gap: 5px; }
  .contact__dot {
    width: 7px; height: 7px; border-radius: 50%;
    background: var(--dark-grey); flex: none;
  }

  .watermark {
    position: absolute; left: 32px; top: 400px;
    width: 190px; height: 190px; border-radius: 50%;
    border: 22px solid var(--watermark);
  }

  .footer-wave { position: absolute; left: 0; bottom: 0; width: 524px; height: 180px; }

  .slogan {
    position: absolute; left: 278px; top: 706px;
    font-family: "Merriweather", Georgia, serif;
    font-weight: 900; font-size: 17px; color: var(--ink);
    letter-spacing: 0.5px; transform: rotate(4deg); transform-origin: left center;
    white-space: nowrap;
  }
</style>
</head>
<body>
  <main class="letterhead">
    <span class="edge-tab edge-tab--left"></span>
    <span class="edge-tab edge-tab--right"></span>

    <header class="brand">
      <span class="brand__mark"></span>
      <span class="brand__name">KORVANE</span>
    </header>

    <ul class="contact">
      <li class="contact__company">Korvane Valves Pte. Ltd. (Singapore)</li>
      <li class="contact__item"><span class="contact__dot"></span>Regd. No. 201947215K</li>
      <li class="contact__item"><span class="contact__dot"></span>(65) 6418 2904</li>
      <li class="contact__item"><span class="contact__dot"></span>(65) 6472 9186</li>
      <li class="contact__item"><span class="contact__dot"></span>sales@korvanevalves.example</li>
      <li class="contact__item"><span class="contact__dot"></span>www.korvanevalves.example</li>
    </ul>

    <div class="watermark" role="img" aria-label="Faint brand watermark"></div>

    <svg class="footer-wave" viewBox="0 0 524 180" aria-hidden="true">
      <defs>
        <linearGradient id="wave-yellow" x1="0" y1="0" x2="1" y2="1">
          <stop offset="0" stop-color="var(--brand-yellow-light)"/>
          <stop offset="1" stop-color="var(--brand-yellow)"/>
        </linearGradient>
        <linearGradient id="wave-grey" x1="0" y1="0" x2="1" y2="0">
          <stop offset="0" stop-color="var(--soft-grey)"/>
          <stop offset="0.6" stop-color="var(--mid-grey)"/>
          <stop offset="1" stop-color="var(--soft-grey)"/>
        </linearGradient>
      </defs>
      <path d="M0 40 C 70 52 110 108 240 112 C 370 116 470 130 524 180 L 0 180 Z" fill="none" stroke="var(--brand-yellow)" stroke-width="2"/>
      <path d="M0 50 C 70 62 110 114 240 118 C 370 122 470 134 524 180 L 0 180 Z" fill="url(#wave-grey)"/>
      <path d="M0 58 C 70 70 112 120 240 124 C 370 128 470 140 524 180 L 0 180 Z" fill="url(#wave-yellow)"/>
    </svg>

    <p class="slogan">MADE WITH PRIDE</p>
  </main>
</body>
</html>
```